Awesome photographers card for an awesome new business

Double sided business card Black background and silver logo in middle on one side. Details on otherside. please keep it simple

Industry/Entity Type

Photographer

Contact Information for Business Card

Gerald Fenwick
0452817360
GeraldFenwickPhotography47@mailbox.test
www.GeraldFenwickPhotography.test.au
Instagram _Gerald_fenwick

Requirements
Must have
• My logo in Silver
• please use instagram logo instead of "Instagram"

```html
<!DOCTYPE html>
<html lang="en">
<head>
<meta charset="utf-8">
<title>Gerald Fenwick Photography – Business Card</title>
<link rel="stylesheet" href="https://fonts.googleapis.com/css2?family=Jost:wght@300;400;600&display=swap">
<style>
  :root {
    --page-bg: #e9e7e3;
    --card-white: #fbfbfa;
    --card-black: #1c1d1d;
    --ink: #1a1a1a;
    --ink-soft: #3a3a3a;
    --silver: #cfd0d2;
    --silver-line: #a9abae;
  }
  * { margin: 0; padding: 0; box-sizing: border-box; }
  html, body {
    width: 1200px;
    height: 911px;
    overflow: hidden;
    background: var(--page-bg);
    font-family: "Jost", sans-serif;
  }
  .sheet {
    position: relative;
    width: 1200px;
    height: 911px;
    display: flex;
    align-items: center;
    justify-content: center;
    gap: 60px;
  }
  .card {
    position: relative;
    width: 520px;
    height: 320px;
    border-radius: 22px;
    overflow: hidden;
    box-shadow: 0 10px 28px rgba(0, 0, 0, 0.18);
  }

  /* Details side */
  .card--details { background: var(--card-white); }
  .details__band {
    position: absolute;
    left: 0; top: 0; bottom: 0;
    width: 58px;
    background: var(--card-black);
  }
  .details__mark {
    position: absolute;
    left: 22px;
    top: 26px;
    width: 74px;
    height: 74px;
    border-radius: 50%;
    background: var(--card-white);
    border: 2px solid var(--silver-line);
  }
  .details__name {
    position: absolute;
    left: 112px;
    top: 46px;
    font-weight: 600;
    font-size: 22px;
    letter-spacing: 0.2px;
    color: var(--ink);
    text-transform: uppercase;
  }
  .details__contacts {
    position: absolute;
    right: 26px;
    bottom: 26px;
    list-style: none;
    display: flex;
    flex-direction: column;
    gap: 4px;
  }
  .contact {
    display: flex;
    align-items: center;
    justify-content: flex-end;
    gap: 12px;
    font-weight: 300;
    font-size: 14px;
    color: var(--ink-soft);
  }
  .contact__icon {
    width: 12px;
    height: 12px;
    flex: none;
  }

  /* Logo side */
  .card--logo {
    background: var(--card-black);
    display: flex;
    align-items: center;
    justify-content: center;
    gap: 14px;
  }
  .logo__circle {
    width: 22px;
    height: 22px;
    border-radius: 50%;
    border: 2px solid var(--silver);
  }
  .logo__name {
    font-weight: 400;
    font-size: 30px;
    letter-spacing: 1px;
    color: var(--silver);
  }
</style>
</head>
<body>
<main class="sheet">
  <section class="card card--details" aria-label="Business card, details side">
    <div class="details__band"></div>
    <div class="details__mark"></div>
    <h1 class="details__name">Gerald Fenwick</h1>
    <ul class="details__contacts">
      <li class="contact">0452817360
        <svg class="contact__icon" viewBox="0 0 12 12" aria-hidden="true"><path d="M3 1l2 2.5-1.2 1.2c.7 1.5 1.9 2.7 3.5 3.5L8.5 7 11 9l-1 2C5.5 11 1 6.5 1 2z" fill="#1a1a1a"/></svg>
      </li>
      <li class="contact">GeraldFenwickPhotography47@mailbox.test
        <svg class="contact__icon" viewBox="0 0 12 12" aria-hidden="true"><rect x="0.5" y="2" width="11" height="8" rx="1" fill="#1a1a1a"/><path d="M1 3l5 3.5L11 3" stroke="#fbfbfa" fill="none"/></svg>
      </li>
      <li class="contact">www.GeraldFenwickPhotography.test.au
        <svg class="contact__icon" viewBox="0 0 12 12" aria-hidden="true"><circle cx="6" cy="6" r="5.3" fill="#1a1a1a"/><path d="M1 6h10M6 .8c-2.2 2.8-2.2 7.6 0 10.4M6 .8c2.2 2.8 2.2 7.6 0 10.4" stroke="#fbfbfa" stroke-width=".8" fill="none"/></svg>
      </li>
      <li class="contact">_Gerald_fenwick
        <svg class="contact__icon" viewBox="0 0 12 12" aria-hidden="true"><rect x="1" y="1" width="10" height="10" fill="#1a1a1a"/></svg>
      </li>
    </ul>
  </section>

  <section class="card card--logo" aria-label="Business card, logo side">
    <div class="logo__circle"></div>
    <p class="logo__name">Gerald Fenwick</p>
  </section>
</main>
</body>
</html>
```